Business Card Design

Hello,
I try and keep my business card fresh and current. So about every year i get a new one. This year I'd like something with a white background and black lettering.
Before you start - I do not want my phone number or any other description on the card other than my url and my email.

I'd like a double sided business card with
TomFarrow.com on one side

and

Tom@TomFarrow.com on the other side of the card

Thinking very minimalistic and modern.
I don't have a particular font i mind or how to capitalize my name or website. This card will lead people to my new website that is being designed to showcase my photography and music.

* Initial thought was the front side of the card having a grid-like pattern built out of dashes or periods, with my website sitting within the pattern and on the back side my email on a stark white background. But that might look completely lame - haha.

I'm looking forward to seeing what you come up with.

thank you,
- tom farrow
Updates

Project Deadline Extended
Reason: Want to spend some more time with the designs and add a little $. thanks for all the designs - tom

Project Deadline Extended

Wanted to add a little $ and spend some more time with the designs.

big thanks to all who have submitted work 

- tom

Industry/Entity Type

Business

Contact Information for Business Card

www.tomfarrow.com
tom@tomfarrow.com

Colors
000000
ffffff

Requirements
Must have
• tomfarrow.com
tom@tomfarrow.com
Should not have
• phone number
any description of what i do, photography or music

```html
<!DOCTYPE html>
<html lang="en">
<head>
<meta charset="utf-8">
<title>Tom Farrow — Business Card</title>
<link rel="stylesheet" href="https://fonts.googleapis.com/css2?family=Open+Sans:wght@300;700&display=swap">
<style>
  :root {
    --backdrop: #9fcfca;
    --card: #fbfbfa;
    --ink: #3a3a3a;
    --frame: #4a4a4a;
    --foil: #8c8c8a;
  }
  html, body {
    margin: 0;
    padding: 0;
    overflow: hidden;
  }
  .canvas {
    position: relative;
    width: 1200px;
    height: 1200px;
    background: var(--backdrop);
    overflow: hidden;
  }
  .card {
    position: absolute;
    left: 324px;
    width: 552px;
    height: 344px;
    background: var(--card);
  }
  .card--back { top: 202px; }
  .card--front { top: 672px; }
  .card__frame {
    position: absolute;
    inset: 0;
    width: 552px;
    height: 344px;
  }
  .card__frame rect {
    fill: none;
    stroke: var(--frame);
    stroke-width: 1.5;
    stroke-dasharray: 5 4;
  }
  .card__text {
    position: absolute;
    inset: 0;
    display: flex;
    align-items: center;
    justify-content: center;
    margin: 0;
    font-family: "Open Sans", sans-serif;
    text-transform: uppercase;
    white-space: nowrap;
  }
  .card__email {
    font-weight: 300;
    font-size: 35px;
    color: var(--ink);
    letter-spacing: 0;
  }
  .card__url {
    font-weight: 700;
    font-size: 37px;
    color: var(--foil);
    letter-spacing: -2px;
  }
</style>
</head>
<body>
  <main class="canvas">
    <section class="card card--back">
      <svg class="card__frame" viewBox="0 0 552 344" aria-hidden="true">
        <rect x="34" y="33" width="488" height="282"/>
      </svg>
      <p class="card__text card__email">Tom@TomFarrow.com</p>
    </section>
    <section class="card card--front">
      <svg class="card__frame" viewBox="0 0 552 344" aria-hidden="true">
        <rect x="34" y="33" width="488" height="282"/>
      </svg>
      <p class="card__text card__url">www.tomfarrow.com</p>
    </section>
  </main>
</body>
</html>
```